QRV Advisors needs a web site

We need a web site for www.qrvadvisors-example.com. QRV is a mergers and acquisition consulting company that focuses our buyer and seller services on logistics companies. We help put companies together, and help with legal and financial due diligence. We want the web site to express our service and show the logistics components. We want personalized images versus pictures of trucks and airplanes.

Our new logo uses Burgandy and grey colors. Image attached. We are not in to bold, big letters...classy, artistic, low key preferred. Confidentiality, experience, professional are what we want to express on the site.

All we expect for the first part of this project is a home page, and one subpage.  We are budgeting other funds for the technical aspects of the web site

Reason: All that I'm seeing so far is trucks, forklifts and planes. We are a legal mergers and acquisitions firm that focus on logistics. I like some of the images to say logistics, but really want it say legal, financial, and putting companies together. Will pay extra for the sub page if someone can impress us with a home page.

Reason: Swamped with another project at the moment...will work on this over the weekend and provide designer feedback and select final design by Tuesday

```html
<!DOCTYPE html>
<html lang="en">
<head>
<meta charset="utf-8">
<title>QRV Advisors – Home</title>
<link rel="stylesheet" href="https://fonts.googleapis.com/css2?family=Open+Sans:wght@400;600&family=Roboto:wght@500;700&family=Exo+2:wght@700&display=swap">
<style>
:root{
  --burgundy:#a5002f;
  --burgundy-dark:#8a0027;
  --ink:#3c3c3c;
  --grey:#6b6b6b;
  --light:#efefef;
  --band-bottom:#2f2f2f;
  --rule:#c9c9c9;
  --white:#ffffff;
}
*{margin:0;padding:0;box-sizing:border-box}
html,body{width:1004px;height:1200px;overflow:hidden;background:var(--white)}
body{position:relative;font-family:"Open Sans",sans-serif;color:var(--ink)}
.abs{position:absolute}

.top-strip{left:0;top:0;width:1004px;height:6px;background:#5b5b5b}
.header{left:0;top:6px;width:1004px;height:119px;background:linear-gradient(90deg,#e9e9e9,#f6f6f6 30%,#f0f0f0)}
.brand{left:116px;top:44px;display:flex;align-items:center;gap:10px;font-family:"Roboto",sans-serif;font-weight:500;font-size:30px;color:var(--burgundy);letter-spacing:1px}
.brand-mark{width:14px;height:14px;background:var(--burgundy)}
.call{left:744px;top:20px;display:flex;gap:8px;align-items:center}
.call-text small{display:block;font-size:11px;color:var(--ink);line-height:1.2}
.call-text strong{display:block;font-family:"Roboto",sans-serif;font-size:17px;color:var(--burgundy);font-weight:700;line-height:1.1}
.nav{left:447px;top:74px;display:flex;gap:15px;list-style:none}
.nav li{font-size:11px;color:var(--grey);border-top:1px solid var(--rule);border-bottom:1px solid var(--rule);padding:5px 2px 6px;position:relative}
.nav li.current{color:var(--burgundy);font-weight:600}
.nav li.current::before{content:"";position:absolute;left:50%;top:-1px;margin-left:-4px;border:4px solid transparent;border-top-color:#555}

.hero{left:0;top:125px;width:1004px;height:371px;background:linear-gradient(90deg,#c9c1b8,#e6e2dc 25%,#8a94a4 50%,#d9d2c9 75%,#6c6f76)}
.hero-arrow{width:38px;height:38px;border-radius:50%;background:#1c1c1c;box-shadow:0 0 0 3px rgba(255,255,255,.35)}
.hero-caption{left:543px;top:378px;width:461px;height:106px;background:rgba(35,35,35,.82);clip-path:polygon(16px 0,100% 0,100% 100%,0 100%)}
.hero-caption p{position:absolute;left:37px;top:6px;font-family:"Exo 2",sans-serif;font-weight:700;font-size:23px;line-height:30px;color:var(--white);letter-spacing:.5px}

.services{left:0;top:496px;width:1004px;height:226px;background:linear-gradient(#4d4d4d,var(--band-bottom));border-top:3px solid #666}
.service{width:160px;text-align:center;color:var(--white)}
.service .disc{width:118px;height:118px;border-radius:50%;background:var(--burgundy);margin:0 auto;display:flex;align-items:center;justify-content:center}
.service h3{font-family:"Roboto",sans-serif;font-weight:500;font-size:14.5px;margin-top:12px}
.service p{font-size:10px;line-height:15px;margin-top:5px}
.band-arrow{top:565px}

.col-title{font-family:"Roboto",sans-serif;font-weight:700;font-size:17px;color:var(--grey);border-bottom:1px dashed #aaa;padding-bottom:4px;width:235px}
.col-title em{font-style:normal;color:var(--burgundy)}
.about-photo{left:118px;top:785px;width:235px;height:102px;border:4px solid var(--burgundy)}
.about-photo div{width:100%;height:100%;background:linear-gradient(90deg,#5f5a58,#cfc6bc 40%,#e8e2da 60%,#6f6a68)}
.about-text{left:119px;top:897px;width:234px;font-size:10.3px;line-height:15.4px}
.more{font-family:"Roboto",sans-serif;font-weight:700;font-size:10px;color:var(--burgundy)}
.news-item{left:386px;width:234px;border-bottom:1px dotted #ddd;padding-bottom:7px}
.news-item .meta{font-size:10.3px;color:var(--burgundy)}
.news-item p{font-size:10.3px;line-height:16px;letter-spacing:.6px;margin-top:1px}
.news-item .more{display:block;text-align:right}
.form-label{left:654px;font-size:11px}
.field{left:710px;width:177px;height:18px;border:1px solid #bbb;background:var(--white)}
.submit{left:710px;top:972px;width:87px;height:21px;background:var(--burgundy);color:var(--white);font-family:"Roboto",sans-serif;font-weight:700;font-size:13px;text-align:center;line-height:21px}

.footer{left:0;top:1032px;width:1004px;height:168px;background:var(--burgundy);border-top:4px solid #5b5b5b}
.foot-title{font-family:"Roboto",sans-serif;font-weight:500;font-size:12.5px;color:var(--white);border-bottom:1px dashed rgba(255,255,255,.6);padding-bottom:4px}
.foot-links{list-style:none;font-size:10.3px;line-height:18.4px;color:var(--white)}
.foot-links li::before{content:"›";margin-right:7px}
.foot-divider{width:1px;background:rgba(255,255,255,.25)}
.foot-contact{font-size:10.3px;line-height:14.5px;color:var(--white)}
.email-box{left:512px;top:1114px;width:169px;height:19px;background:var(--white);border-radius:2px;font-size:10px;color:#888;padding:2px 0 0 25px}
.subscribe{left:513px;top:1145px;width:67px;height:19px;background:#555;color:var(--white);border-radius:2px;font-family:"Roboto",sans-serif;font-weight:700;font-size:11px;text-align:center;line-height:19px}
.foot-brand{left:710px;top:1052px;font-family:"Roboto",sans-serif;font-weight:500;font-size:40px;color:#d8d8d8;letter-spacing:4px}
.social{width:21px;height:21px;border-radius:3px;background:#3f7cc4;box-shadow:inset 0 0 0 2px rgba(255,255,255,.4)}
.copyright{left:702px;top:1153px;width:200px;text-align:center;font-size:10.3px;line-height:15px;color:var(--white)}
</style>
</head>
<body>

<div class="abs top-strip"></div>
<header class="abs header"></header>
<div class="abs brand"><span class="brand-mark"></span>QRV Advisors</div>
<div class="abs call">
  <svg width="28" height="28" viewBox="0 0 28 28"><circle cx="14" cy="14" r="12.5" fill="none" stroke="#a5002f" stroke-width="2"/><path d="M10 8c-2 2-1 7 3 10s7 4 8 2l-2-3-2 1c-2-1-4-3-5-5l1-2z" fill="#a5002f"/></svg>
  <div class="call-text"><small>Call Us Today</small><strong>555 014 2290</strong></div>
</div>
<ul class="abs nav">
  <li class="current">Home</li><li>About Us</li><li>Consulting Services</li><li>News &amp; Events</li><li>FAQ's</li><li>Contact Us</li>
</ul>

<section class="abs hero" role="img" aria-label="Photo of a smiling team of business consultants in suits"></section>
<div class="abs hero-arrow" style="left:118px;top:280px"><svg width="38" height="38"><path d="M22 12l-7 7 7 7" fill="none" stroke="#fff" stroke-width="2"/></svg></div>
<div class="abs hero-arrow" style="left:848px;top:280px"><svg width="38" height="38"><path d="M16 12l7 7-7 7" fill="none" stroke="#fff" stroke-width="2"/></svg></div>
<div class="abs hero-caption"><p>We Are Mergers &amp;<br>Acquisition&nbsp; Technology<br>Consulting Company.</p></div>

<section class="abs services"></section>
<svg class="abs band-arrow" style="left:94px" width="16" height="28"><path d="M13 2L3 14l10 12" fill="none" stroke="#999" stroke-width="2"/></svg>
<svg class="abs band-arrow" style="left:890px" width="16" height="28"><path d="M3 2l10 12-10 12" fill="none" stroke="#999" stroke-width="2"/></svg>

<div class="abs service" style="left:134px;top:521px">
  <div class="disc"><svg width="64" height="64" viewBox="0 0 64 64" fill="#fff"><rect x="6" y="30" width="5" height="26"/><rect x="14" y="38" width="5" height="18"/><rect x="22" y="34" width="5" height="22"/><rect x="30" y="42" width="5" height="14"/><rect x="38" y="36" width="5" height="20"/><circle cx="38" cy="18" r="11" fill="none" stroke="#fff" stroke-width="4"/><path d="M45 26l10 12" stroke="#fff" stroke-width="5"/></svg></div>
  <h3>Business Analysis</h3><p>Lorem ipsum dolor sit ameteuis tincidunt ut laoreet amte</p>
</div>
<div class="abs service" style="left:326px;top:521px">
  <div class="disc"><svg width="90" height="64" viewBox="0 0 90 64" fill="#fff"><circle cx="20" cy="20" r="8"/><path d="M6 50c0-14 6-20 14-20s14 6 14 20z"/><circle cx="70" cy="20" r="8"/><path d="M56 50c0-14 6-20 14-20s14 6 14 20z"/><circle cx="45" cy="16" r="10"/><path d="M27 52c0-17 8-24 18-24s18 7 18 24z"/></svg></div>
  <h3>Business Intelligence</h3><p>Lorem ipsum dolor sit ameteuis tincidunt ut laoreet amte</p>
</div>
<div class="abs service" style="left:518px;top:521px">
  <div class="disc"><svg width="64" height="80" viewBox="0 0 64 80" fill="#fff"><path d="M32 4L16 34h10v6C26 54 18 62 12 74h12c4-8 8-14 8-20 0 6 4 12 8 20h12C46 62 38 54 38 40v-6h10z"/></svg></div>
  <h3>Mergers</h3><p>Lorem ipsum dolor sit ameteuis tincidunt ut laoreet amte</p>
</div>
<div class="abs service" style="left:710px;top:521px">
  <div class="disc"><svg width="76" height="64" viewBox="0 0 76 64" fill="#fff"><path d="M50 6l22 20-22 20V34H34V18h16z"/><path d="M26 18L4 38l22 20V46h16V30H26z"/></svg></div>
  <h3>Acquisition</h3><p>Lorem ipsum dolor sit ameteuis tincidunt ut laoreet amte</p>
</div>

<h2 class="abs col-title" style="left:118px;top:747px"><em>ABOUT</em> COMPANY</h2>
<div class="abs about-photo"><div role="img" aria-label="Photo of a diverse group of smiling professionals"></div></div>
<p class="abs about-text">QRV assists business owners within the logistics industry to implement growth and exit strategies. We offer business planning and merger and acquisition(M&amp;A) advisory services. QRV services are offered by industry executives with extensive M&amp;A experience..</p>
<span class="abs more" style="left:294px;top:984px">Read More »</span>

<h2 class="abs col-title" style="left:386px;top:747px"><em>NEWS &amp;</em> EVENTS</h2>
<div class="abs news-item" style="top:783px"><span class="meta">8-10-2014 | By Admin</span><p>Lorem ipsum dolor sit amet, consectetuer adipiscing elit, sed diam...</p><span class="more">Read More »</span></div>
<div class="abs news-item" style="top:859px"><span class="meta">8-10-2014 | By Admin</span><p>Lorem ipsum dolor sit amet, consectetuer adipiscing elit, sed diam...</p><span class="more">Read More »</span></div>
<div class="abs news-item" style="top:937px;border-bottom:none"><span class="meta">8-10-2014 | By Admin</span><p>Lorem ipsum dolor sit amet, consectetuer adipiscing elit, sed diam...</p><span class="more">Read More »</span></div>

<h2 class="abs col-title" style="left:652px;top:747px"><em>CONTACT</em> US</h2>
<span class="abs form-label" style="top:787px">Name</span><div class="abs field" style="top:785px"></div>
<span class="abs form-label" style="top:822px">Phone</span><div class="abs field" style="top:820px"></div>
<span class="abs form-label" style="top:857px">Email</span><div class="abs field" style="top:856px"></div>
<span class="abs form-label" style="top:892px">Message</span><div class="abs field" style="top:891px;height:57px"></div>
<div class="abs submit">SUBMIT</div>

<footer class="abs footer"></footer>
<h4 class="abs foot-title" style="left:118px;top:1050px;width:111px">QUICK LINKS</h4>
<ul class="abs foot-links" style="left:118px;top:1074px">
  <li>Home</li><li>About Us</li><li>Consulting Services</li><li>News &amp; Events</li><li>FAQ's</li><li>Contact Us</li>
</ul>
<div class="abs foot-divider" style="left:245px;top:1052px;height:128px"></div>
<h4 class="abs foot-title" style="left:272px;top:1050px;width:190px">CONTACT US</h4>
<svg class="abs" style="left:274px;top:1080px" width="12" height="18" viewBox="0 0 12 18"><path d="M6 0a6 6 0 016 6c0 4-6 12-6 12S0 10 0 6a6 6 0 016-6z" fill="#fff"/><circle cx="6" cy="6" r="2.2" fill="#a5002f"/></svg>
<p class="abs foot-contact" style="left:301px;top:1077px;width:180px">Lorem ipsum dolor sit ameteuismo tincidunt ut laoreet dolore my amte,</p>
<svg class="abs" style="left:274px;top:1119px" width="14" height="14" viewBox="0 0 14 14"><path d="M3 1c-2 2-1 6 2 9s7 4 8 2l-2-3-2 1C7 9 5 7 4 5l1-2z" fill="#fff"/></svg>
<p class="abs foot-contact" style="left:301px;top:1119px">555-014-2290</p>
<svg class="abs" style="left:273px;top:1151px" width="16" height="11" viewBox="0 0 16 11"><rect width="16" height="11" fill="#fff"/><path d="M0 0l8 6 8-6" fill="none" stroke="#a5002f" stroke-width="1.3"/></svg>
<p class="abs foot-contact" style="left:301px;top:1148px">info@qrvadvisors-example.com</p>
<div class="abs foot-divider" style="left:489px;top:1052px;height:128px"></div>
<h4 class="abs foot-title" style="left:513px;top:1050px;width:179px">NEWSLETTER</h4>
<p class="abs foot-contact" style="left:513px;top:1078px;width:185px">Subscribe to our newsletter to receive our special offers , discounts &amp; more.</p>
<div class="abs email-box">your e-mail address</div>
<div class="abs subscribe">Subscribe</div>
<div class="abs foot-brand">QRV</div>
<div class="abs social" style="left:766px;top:1121px"></div>
<div class="abs social" style="left:795px;top:1121px;background:#4fb3e6"></div>
<div class="abs social" style="left:823px;top:1121px;background:#1f7fb8"></div>
<p class="abs copyright">© 2014 qrvadvisors-example.com<br>All Rights Reserved</p>

</body>
</html>
```